Support People to improve their image and well-being by provided personalised advise

We need a design for business cards that could be used for production on plano press. We build a new business in our region for advising mostly women (also men though) on style embracing several aspects including fashion, style, self-confidence and ultimately your internal and external image. The business card should be "classy", "french-style". The business is located in the french -speaking part of Switzerland, close to France. The name of the company is Lomu Grace

Target Market(s)

Service fees won't be cheap (medium to premium) thus we target mid-class to upper-class women (1st target) and men (2nd target)

Industry/Entity Type

Life Coaching

Contact Information for Business Card

Conseil en Image

+41 76 418 63 07
tovasel@lomu-grace.example
connectly.example/in/sel-moran-tova

Logo Text

Lomu Grace

Colors

Designer to choose colors to be used in the design.

```html
<!DOCTYPE html>
<html lang="en">
<head>
<meta charset="utf-8">
<title>Lomu Grace — Business Card</title>
<link rel="stylesheet" href="https://fonts.googleapis.com/css2?family=Lato:wght@400;700&display=swap">
<style>
  :root {
    --plum: #731c72;
    --magenta: #ac1cab;
    --magenta-mid: #9b1c9a;
    --white: #ffffff;
    --stage: #eeeaec;
    --logo-plum: #7a1f74;
  }
  html, body {
    margin: 0;
    padding: 0;
    width: 1200px;
    height: 900px;
    overflow: hidden;
    background: var(--stage);
    font-family: "Lato", sans-serif;
  }
  .canvas {
    position: relative;
    width: 1200px;
    height: 900px;
  }
  .card {
    position: absolute;
    box-shadow: 0 6px 18px rgba(0,0,0,0.18);
  }
  .card-front {
    left: 178px;
    top: 74px;
    width: 588px;
    height: 364px;
    background: linear-gradient(105deg, var(--magenta) 0%, var(--magenta-mid) 40%, var(--plum) 58%, var(--plum) 100%);
    overflow: hidden;
    color: var(--white);
  }
  .front-brand {
    position: absolute;
    left: 34px;
    top: 160px;
    font-size: 34px;
    font-weight: 700;
    color: var(--white);
    letter-spacing: 0.5px;
  }
  .identity {
    position: absolute;
    right: 38px;
    top: 62px;
    text-align: right;
  }
  .person-name {
    margin: 0;
    font-size: 21px;
    font-weight: 700;
    letter-spacing: 0.3px;
    text-transform: uppercase;
    line-height: 1.1;
  }
  .person-role {
    margin: 2px 0 0;
    font-size: 16px;
    font-weight: 400;
  }
  .contacts {
    position: absolute;
    right: 34px;
    top: 215px;
    list-style: none;
    margin: 0;
    padding: 0;
    text-align: right;
    font-size: 15.5px;
  }
  .contacts li {
    display: flex;
    justify-content: flex-end;
    align-items: center;
    gap: 4px;
    height: 22px;
    white-space: nowrap;
  }
  .contacts li.social {
    margin-top: 24px;
  }
  .contact-icon {
    width: 16px;
    height: 16px;
    flex: none;
  }
  .social-dot {
    width: 20px;
    height: 20px;
    border-radius: 50%;
    background: var(--white);
    flex: none;
  }
  .card-back {
    left: 388px;
    top: 505px;
    width: 567px;
    height: 352px;
    background: var(--white);
  }
  .back-brand {
    position: absolute;
    left: 0;
    right: 0;
    top: 150px;
    text-align: center;
    font-size: 40px;
    font-weight: 400;
    color: var(--logo-plum);
    letter-spacing: 1px;
  }
</style>
</head>
<body>
<main class="canvas">
  <section class="card card-front" aria-label="Business card front">
    <div class="front-brand">Lomu Grace</div>
    <div class="identity">
      <h1 class="person-name">Tova Moran</h1>
      <p class="person-role">Managing Director</p>
    </div>
    <ul class="contacts">
      <li>+41 76 418 63 07
        <svg class="contact-icon" viewBox="0 0 16 16" aria-hidden="true">
          <path d="M2 6 Q8 1 14 6 L12 8 L10 6.5 L6 6.5 L4 8 Z" fill="#fff"/>
          <rect x="4" y="8" width="8" height="5" rx="1" fill="#fff"/>
        </svg>
      </li>
      <li>tovasel@lomu-grace.example
        <svg class="contact-icon" viewBox="0 0 16 16" aria-hidden="true">
          <rect x="2" y="4" width="12" height="9" fill="#fff"/>
          <path d="M2 4 L8 9 L14 4" fill="none" stroke="#731c72" stroke-width="1.2"/>
        </svg>
      </li>
      <li class="social">connectly.example/in/sel-moran-tova
        <span class="social-dot" aria-hidden="true"></span>
      </li>
    </ul>
  </section>

  <section class="card card-back" aria-label="Business card back">
    <div class="back-brand">Lomu Grace</div>
  </section>
</main>
</body>
</html>
```